kelvaro stationary business card and letterhead

THIS PROJECT IS TO DESIGN A BUSINESS CARD DOUBLE SIDES .

Reason: I AM WAITING FOR TESINU SUBMISION

Industry/Entity Type

Business

Font styles to use
Other font styles liked:
• Chose your font

```html
<!DOCTYPE html>
<html lang="en">
<head>
<meta charset="utf-8">
<title>kelvaro stationery – business card and letterhead</title>
<link rel="stylesheet" href="https://fonts.googleapis.com/css2?family=Open+Sans:wght@400;600&display=swap">
<style>
  :root {
    --backdrop: #e8e8e8;
    --paper: #fbfbfb;
    --brand-yellow: #e0b00f;
    --brand-dark: #2a2a2c;
    --ink: #3a3a3a;
    --ink-soft: #6b6b6b;
  }
  * { box-sizing: border-box; margin: 0; padding: 0; }
  html, body { width: 1200px; height: 1000px; overflow: hidden; }
  body {
    background: var(--backdrop);
    position: relative;
    font-family: "Open Sans", Arial, sans-serif;
    color: var(--ink);
  }

  .company-name {
    font-family: "Open Sans", Arial, sans-serif;
    font-weight: 600;
    font-size: 24px;
    line-height: 1;
    color: var(--brand-dark);
  }

  .contact-list { list-style: none; font-size: 7px; line-height: 1.6; color: var(--ink); }
  .contact-list li { display: flex; align-items: center; gap: 5px; white-space: nowrap; }
  .contact-icon { width: 6px; height: 6px; border-radius: 50%; background: var(--brand-yellow); flex: none; }
  .contact-icon.is-blank { visibility: hidden; }

  /* Letterhead */
  .letterhead {
    position: absolute; left: 560px; top: 70px;
    width: 590px; height: 834px;
    background: var(--paper);
    box-shadow: 0 2px 10px rgba(0,0,0,0.12);
  }
  .letterhead .company-name { position: absolute; left: 70px; top: 64px; }
  .letterhead .contact-list { position: absolute; left: 450px; top: 200px; }
  .letter-body {
    position: absolute; left: 70px; top: 130px; width: 350px;
    font-size: 8px; line-height: 1.6; color: var(--ink-soft);
  }
  .letter-body p { margin-bottom: 10px; }
  .signature {
    position: absolute; left: 220px; top: 560px;
    width: 120px; height: 36px;
    background: linear-gradient(90deg, rgba(42,42,44,0.10), rgba(42,42,44,0.04));
    border-radius: 4px;
  }
  .letter-footer {
    position: absolute; left: 0; right: 0; bottom: 0; height: 28px;
    display: flex;
  }
  .letter-footer-dark { width: 32%; background: var(--brand-dark); }
  .letter-footer-yellow { flex: 1; background: var(--brand-yellow); }

  /* Business cards */
  .card {
    position: absolute; width: 440px; height: 252px;
    box-shadow: 0 2px 8px rgba(0,0,0,0.12);
    overflow: hidden;
  }
  .card-front {
    left: 60px; top: 400px;
    background: var(--brand-yellow);
    display: flex; align-items: center; justify-content: center;
  }
  .card-front .company-name { font-size: 32px; }

  .card-back { left: 60px; top: 700px; background: var(--paper); }
  .card-back-band {
    position: absolute; left: 0; top: 0; width: 240px; height: 16px;
    background: var(--brand-yellow);
  }
  .card-holder { position: absolute; left: 34px; top: 70px; }
  .holder-name { font-size: 22px; font-weight: 400; color: var(--brand-dark); }
  .holder-title { font-size: 9px; font-weight: 600; color: var(--brand-yellow); margin: 2px 0 10px; }
  .card-back .company-name { position: absolute; right: 34px; top: 116px; font-size: 17px; }
</style>
</head>
<body>

<section class="letterhead" aria-label="Letterhead">
  <div class="company-name">kelvaro</div>

  <ul class="contact-list">
    <li><span class="contact-icon"></span>18 Orchard Lane, Bellmoor,</li>
    <li><span class="contact-icon is-blank"></span>Postal Code, Country</li>
    <li><span class="contact-icon"></span>555-0142-388</li>
    <li><span class="contact-icon"></span>555-0142-390</li>
    <li><span class="contact-icon"></span>hello@kelvaro.com</li>
    <li><span class="contact-icon"></span>www.kelvaro.com</li>
  </ul>

  <div class="letter-body">
    <p>Dear Client</p>
    <p>Lorem ipsum dolor sit amet, consectetur adipiscing elit. Nulla sodales nisi vitae lorem ipsum dolor sit amet, consectetur adipiscing elit. Suspendisse feugiat eros nisi, a facilisis risus eleifend sed. Aliquam mauris enim, fermentum eu lacinia sit amet, laoreet eu leo. Nullam eleifend nulla in libero tristique, ac vulputate odio tincidunt.</p>
    <p>Nullam aliquam ligula ac sem aliquet varius. Nullam sed laoreet sapien. Fusce ultricies lobortis odio, sed imperdiet magna lacinia egestas. Morbi vitae varius nibh. Phasellus purus felis, congue id tempor quis, porttitor ut sem. Integer turpis nunc, posuere at quam interdum, interdum pharetra lectus.</p>
    <p>Pellentesque habitant morbi tristique senectus et netus et malesuada fames ac turpis egestas. Donec quis fermentum massa. Vivamus auctor tincidunt tellus, vel iaculis elit sagittis sit amet. Sed dignissim sapien sed rhoncus imperdiet.</p>
    <p>Best regards,</p>
  </div>

  <div class="signature" role="img" aria-label="Handwritten signature of the sender"></div>

  <div class="letter-footer">
    <div class="letter-footer-dark"></div>
    <div class="letter-footer-yellow"></div>
  </div>
</section>

<section class="card card-front" aria-label="Business card front">
  <div class="company-name">kelvaro</div>
</section>

<section class="card card-back" aria-label="Business card back">
  <div class="card-back-band"></div>
  <div class="card-holder">
    <div class="holder-name">Dara Voss</div>
    <div class="holder-title">Managing Director</div>
    <ul class="contact-list">
      <li><span class="contact-icon"></span>18 Orchard Lane, Bellmoor Postal Code, Country</li>
      <li><span class="contact-icon"></span>555-0142-388</li>
      <li><span class="contact-icon"></span>555-0142-390</li>
      <li><span class="contact-icon"></span>hello@kelvaro.com</li>
      <li><span class="contact-icon"></span>www.kelvaro.com</li>
    </ul>
  </div>
  <div class="company-name">kelvaro</div>
</section>

</body>
</html>
```